Logo and Card design for KRV Home Solutions LLC

I need an edgier logo and business card designs. Current logo attached. I like the colors below. I would like the logo to incorporate a home in the design.
Title = Principal-Acquisitions
Email:KRVHOMESOLUTIONS@fernmail.example
555-214-0937
facebook
IG
2 sided business card with the front being contact info a slogan about selling a home fast. The back incorporating What we do. Buy houses, land, or commercial property as is. We find solutions to make the process of selling simple and fair.

Target Market(s)

Motivated house sellers.

Industry/Entity Type

Business

Contact Information for Business Card

Who we are: We are a Faith based Real Estate Investment Company. We pay cash for homes in any condition and can close quick. Whatever the reason you need to sell fast, we can help. We believe in creating win-win solutions to help you in your time of need. We care! We can help!

Logo Text

KRV Home Solutions LLC

Font styles to use
Sans Serif

Colors
33a6d7
0355a3
85abd2
cee9f5
9d9d9d
b2b2b2
ffffff

Requirements
Must have
• Old logo attached. I want something edgier.
• Company name, phone number, description on the back of what we can do. Pay all cash. Buy in as is condition. No fees,Commisions or closing costs.Close quick. No hassles with solutions to meet your unique situation.
• Call today for an offer within 24 hours.

```html
<!DOCTYPE html>
<html lang="en">
<head>
<meta charset="UTF-8">
<title>KRV Home Solutions – Business Card</title>
<link href="https://fonts.googleapis.com/css2?family=Montserrat:wght@600;700&family=Work+Sans:wght@400;500&display=swap" rel="stylesheet">
<style>
  :root {
    --stage: #2b2b2d;
    --navy: #223c85;
    --navy-deep: #1b3272;
    --band-blue: #0355a3;
    --grey-text: #6b6b6b;
    --grey-strip: #9d9d9d;
    --paper: #ffffff;
  }
  * { box-sizing: border-box; margin: 0; padding: 0; }
  html, body { width: 1200px; height: 900px; overflow: hidden; }
  body {
    background: var(--stage);
    font-family: "Work Sans", sans-serif;
    display: flex;
    flex-direction: column;
    align-items: center;
    justify-content: center;
    gap: 36px;
  }
  .card {
    position: relative;
    width: 700px;
    height: 400px;
    overflow: hidden;
  }

  /* Back side */
  .card--back {
    background: linear-gradient(135deg, var(--navy) 0%, var(--navy-deep) 100%);
    color: var(--paper);
    display: flex;
    flex-direction: column;
    align-items: center;
    justify-content: center;
    gap: 44px;
  }
  .brand {
    display: flex;
    align-items: center;
    gap: 14px;
    font-family: "Montserrat", sans-serif;
    font-weight: 700;
    letter-spacing: 0.5px;
  }
  .brand__mark { width: 22px; height: 22px; background: currentColor; }
  .brand__name { font-size: 34px; }
  .offer {
    text-align: center;
    font-size: 17px;
    line-height: 1.45;
    max-width: 520px;
    letter-spacing: 0.3px;
  }

  /* Front side */
  .card--front { background: var(--paper); }
  .front__logo {
    position: absolute;
    left: 60px;
    top: 150px;
    color: var(--navy);
  }
  .front__logo .brand__name { font-size: 26px; }
  .front__divider {
    position: absolute;
    left: 330px;
    top: 70px;
    width: 1.5px;
    height: 190px;
    background: var(--navy);
  }
  .front__details {
    position: absolute;
    left: 352px;
    top: 66px;
  }
  .company {
    font-family: "Montserrat", sans-serif;
    font-weight: 700;
    font-size: 24px;
    color: var(--navy);
    letter-spacing: 0.4px;
  }
  .title {
    font-size: 15px;
    color: var(--grey-text);
    margin-top: 2px;
  }
  .contacts {
    list-style: none;
    margin-top: 34px;
    display: flex;
    flex-direction: column;
    gap: 5px;
    font-size: 15px;
    color: #3d3d3d;
  }
  .contacts li { display: flex; align-items: center; gap: 10px; }
  .contacts svg { width: 14px; height: 14px; flex: none; }
  .dot { width: 12px; height: 12px; border-radius: 50%; background: var(--navy); flex: none; margin: 0 1px; }
  .front__band { position: absolute; left: 0; bottom: 0; width: 700px; height: 120px; }
  .slogan {
    position: absolute;
    right: 34px;
    bottom: 22px;
    font-family: "Montserrat", sans-serif;
    font-weight: 600;
    font-size: 17px;
    letter-spacing: 2.5px;
    color: var(--paper);
  }
</style>
</head>
<body>

  <section class="card card--back" aria-label="Card back">
    <div class="brand">
      <span class="brand__mark"></span>
      <span class="brand__name">KRV HOME SOLUTIONS</span>
    </div>
    <p class="offer">
      Pay all cash. Buy in as is condition. No fees,Commisions
      or closing costs.Close quick. No hassles with solutions
      to meet your unique situation.<br>
      Call today for an offer within 24 hours.
    </p>
  </section>

  <section class="card card--front" aria-label="Card front">
    <div class="front__logo brand">
      <span class="brand__mark"></span>
      <span class="brand__name">KRV HOME</span>
    </div>

    <div class="front__divider"></div>

    <div class="front__details">
      <h1 class="company">KRV HOME SOLUTIONS</h1>
      <p class="title">Principal-Acquisitions</p>
      <ul class="contacts">
        <li>
          <svg viewBox="0 0 14 14" aria-hidden="true"><circle cx="7" cy="7" r="7" fill="#223c85"/><path d="M4.6 3.6l1.3-.3.7 1.7-.8.6a5 5 0 0 0 2.5 2.5l.6-.8 1.7.7-.3 1.3c-3 .4-6.1-2.7-5.7-5.7z" fill="#fff"/></svg>
          555-214-0937
        </li>
        <li><span class="dot"></span>/krvhomesolutions</li>
        <li><span class="dot"></span>@krvhomesolutions</li>
        <li>
          <svg viewBox="0 0 14 14" aria-hidden="true"><circle cx="7" cy="7" r="7" fill="#223c85"/><rect x="3.5" y="4.5" width="7" height="5" rx=".6" fill="none" stroke="#fff" stroke-width="1"/><path d="M3.7 4.8L7 7.4l3.3-2.6" fill="none" stroke="#fff" stroke-width="1"/></svg>
          KRVHOMESOLUTIONS@fernmail.example
        </li>
      </ul>
    </div>

    <svg class="front__band" viewBox="0 0 700 120" preserveAspectRatio="none" aria-hidden="true">
      <polygon points="0,108 395,52 392,120 0,120" fill="var(--grey-strip)"/>
      <polygon points="408,50 700,8 700,120 390,120" fill="var(--band-blue)"/>
    </svg>
    <p class="slogan">SELLING A HOME FAST</p>
  </section>

</body>
</html>
```